Design the 21st Harborlight Open Cinema Showcase Poster. Think modern, chic, cool, film, movies - driving people to the film festival - the film festivla is in San Francisco and the SF East Bay. Our logo is attached. Dates will be determined soon . please use - November 2 - 11, 2018 (for placement) Keep in mind abstract, chic, modern - eye catching. website is www.hlocs-fest.org

Target Market(s)

25 - 45 year old - upper middle class

Industry/Entity Type

Film Production

Colors

Designer to choose colors to be used in the design.

Requirements
Must have
• logo (attached) www.hlocs-fest.org - chic modern design
Nice to have
• best coolest poster ever!
Should not have
• CLIP ART!!!

```html
<!DOCTYPE html>
<html lang="en">
<head>
<meta charset="utf-8">
<title>21st Harborlight Open Cinema Showcase – Poster</title>
<link rel="stylesheet" href="https://fonts.googleapis.com/css2?family=Teko:wght@300;400;500&display=swap">
<style>
  :root {
    --steel-dark: #3b3b3b;
    --steel-mid: #9a9a9a;
    --steel-light: #e2e2e2;
    --ink: #3a3a3a;
    --festival-red: #cf0a0a;
    --paper-white: #ffffff;
  }
  html, body {
    margin: 0;
    padding: 0;
    overflow: hidden;
  }
  .poster {
    position: relative;
    width: 807px;
    height: 1200px;
    overflow: hidden;
    background: linear-gradient(90deg,
      #6a6a6a 0%,
      var(--steel-light) 28%,
      #c9c9c9 50%,
      var(--steel-mid) 72%,
      var(--steel-dark) 100%);
    font-family: "Teko", "Arial Narrow", sans-serif;
  }
  .poster-art {
    position: absolute;
    inset: 0;
    width: 807px;
    height: 1200px;
  }
  .tagline, .title, .dates, .signoff {
    font-family: "Teko", "Arial Narrow", sans-serif;
  }
  .tagline { font-weight: 400; }
  .title { font-weight: 400; }
  .dates { font-weight: 300; }
  .signoff { font-weight: 400; }
  .ink { fill: var(--ink); }
  .accent { fill: var(--festival-red); }
  .knockout { fill: var(--paper-white); }
</style>
</head>
<body>
<main class="poster">
  <svg class="poster-art" viewBox="0 0 807 1200" width="807" height="1200" xmlns="http://www.w3.org/2000/svg">
    <defs>
      <radialGradient id="reel-tone" cx="42%" cy="40%" r="65%">
        <stop offset="0%" stop-color="#8a8a8a"/>
        <stop offset="45%" stop-color="#2a2a2a"/>
        <stop offset="100%" stop-color="#0d0d0d"/>
      </radialGradient>
      <radialGradient id="reel-shadow" cx="50%" cy="50%" r="50%">
        <stop offset="0%" stop-color="#000" stop-opacity="0.45"/>
        <stop offset="100%" stop-color="#000" stop-opacity="0"/>
      </radialGradient>
    </defs>

    <!-- Key visual -->
    <g class="key-visual">
      <ellipse class="key-visual-area" role="img"
        aria-label="Illustration of a glossy black film strip spiralling into a floating sphere"
        cx="400" cy="335" rx="175" ry="205" fill="url(#reel-tone)"/>
      <ellipse class="key-visual-shadow" cx="400" cy="597" rx="105" ry="11" fill="url(#reel-shadow)"/>
    </g>

    <!-- Tagline -->
    <text class="tagline" font-size="25">
      <tspan class="ink" x="234" y="657">SOMETHING FOR </tspan><tspan class="accent">EVERYONE</tspan>
    </text>
    <text class="tagline" font-size="25" text-anchor="end">
      <tspan class="ink" x="571" y="684">FROM AROUND </tspan><tspan class="accent">THE WORLD</tspan>
    </text>

    <!-- Festival title -->
    <text class="title accent" x="126" y="840" font-size="178" textLength="232" lengthAdjust="spacingAndGlyphs">21ST</text>
    <text class="title ink" x="280" y="843" font-size="58" textLength="192" lengthAdjust="spacingAndGlyphs"><tspan class="knockout">HA</tspan>RBORLIGHT</text>
    <text class="title ink" x="300" y="893" font-size="58" text-anchor="end">OPEN</text>
    <text class="title accent" font-size="15" transform="translate(318 895) rotate(-90)" textLength="44" lengthAdjust="spacingAndGlyphs">CINEMA</text>
    <text class="title ink" x="322" y="956" font-size="58" textLength="172" lengthAdjust="spacingAndGlyphs">SHOWCASE</text>

    <!-- Dates -->
    <text class="dates accent" x="322" y="1010" font-size="42" textLength="362" lengthAdjust="spacing">NOVEMBER 2-11,</text>
    <text class="dates ink" x="322" y="1074" font-size="42" textLength="116" lengthAdjust="spacing">2018</text>

    <!-- Sign-off: festival mark and website -->
    <g class="signoff">
      <circle class="signoff-mark accent" cx="138" cy="1136" r="9"/>
      <text class="signoff-name ink" x="156" y="1145" font-size="26">HARBORLIGHT OPEN CINEMA SHOWCASE</text>
      <text class="signoff-web ink" x="682" y="1145" font-size="26" text-anchor="end">www.hlocs-fest.org</text>
    </g>
  </svg>
</main>
</body>
</html>
```